LIFE CHANGING NEW WEBSITE DESIGN NEEDED FOR FULL WEBSITE- FUN/FEMININE!

I need a website designed for a personal financial advice website geared at women called BLUE OTTER LANTERN. I will be providing free financial advice around topics of making, saving, spending and sharing money. The concept is to change the way women understand money and the necessity around building various passive income streams to ensure full financial freedom. This will then carry down to advice for mothers with children and children in particular. The website should be elegant and yet witty. I don't want lots of serious photos but more relatable. I will have a photo of myself and my story as this is a blog and needs to be relatable to women and mothers. I like pinks and greys. I want to have a pink piggy bank being broken with a hammer in the front screen to break our traditional mindset around piggy bank saving/spending habits. I have created a logo that is a pink piggy head with BLUE OTTER LANTERN that needs to be incorporated so that it blends into the heading. I have also already started designing the website on Squarespace and can provide access to that. Basically it should have a format of BLUE OTTER LANTERN LOGO center in header then on left hand navigation: MAKE, SAVE, SPEND, SHARE then on right hand header navigation: MISSION, GET STARTED, CONTACT BOL I would like to have the front page when you go to the url to have the image of the piggy bank being broken then a catchy phrase then under 4 boxes with MAKE (image and description) SAVE (image and description) SPEND (image and description) SHARE (image and description) if you click on those or the title they go to pages that are dedicated to each them. Each page should have a little intro on the topic then I want lots of blog links as I will be mainly writing blogs. Each blog site should have ability to write comments as well. I need social media icons on each page too. Please let me know what you need from me to get started. I prefer having a discussion if possible to not waste anyone's time. I need the site to be easy for me to use and add blogs/urls etc as needed. I also need the site to be put into my domain that I already purchased: www.blueotterlantern-sample.com

Target Market(s)

teenage girls, 20 something girls, 30 something girls and mothers

Coding

Coded - Design and coding required

Number of Pages Required

5+ page

Font styles to use
Sans Serif

Colors
e667a6
e34197
f59195
eea4c8
aaaaaa
cbcbcb
959595

Requirements
Must have
• TOP NAVIGATION
• MAKE SAVE SPEND SHARE LOGO/BLUE OTTER LANTERN MISSION GET STARTED CONTACT BOL
• FRONT PAGE: IMAGE OF PIGGY BANK BEING BROKEN WITH A HAMMER
• CATCH PHRASE OVER THE IMAGE
• BUTTON IN PINK- TAKE ACTION (WHICH DIRECTS TO TAKE ACTION TAB ON NAVIGATION HEADER
• 4 BOXES BELOW MAIN IMAGE WITH IMAGE/DESCRIPTIONS FOR MAKE, SAVE, SPEND, SHARE THAT EACH GO TO THE PAGES FROM THE NAVIGATION HEADER
• EACH PAGE SHOULD BE DEDICATED TO THOSE TOPICS THEN THERE IS AN INTRO ON EACH PAGE THEN THE LINKS TO DIFFERENT BLOGS AROUND EACH TOPIC FOR MAKE, SAVE, SPEND, SHARE
• EACH BLOG SHOULD HAVE COMMENTS SECTION AND SOCIAL MEDIA ICONS
• (GOOD TO USE PINKS/GREYS)
Should not have
• BE SUPER BUSY, CLUTTERED, FEEL LIKE I AM SELLING SOMETHING

```html
<!DOCTYPE html>
<html lang="en">
<head>
<meta charset="utf-8">
<title>Blue Otter Lantern – Free Financial Advice</title>
<link href="https://fonts.googleapis.com/css2?family=Montserrat:wght@400;500;600;700&family=Lato:wght@400;700&display=swap" rel="stylesheet">
<style>
:root{
  --pink:#e34197;
  --pink-soft:#e667a6;
  --coral:#f08a95;
  --blush:#eea4c8;
  --grey:#959595;
  --grey-light:#cbcbcb;
  --ink:#2a2a2a;
  --navy:#1f2b4a;
  --footer:#f4f4f5;
  --head:'Montserrat',sans-serif;
  --body:'Lato',sans-serif;
}
*{box-sizing:border-box;margin:0;padding:0}
html,body{width:1200px;height:3611px;overflow:hidden}
body{position:relative;font-family:var(--body);color:var(--ink);background:#fff}
.abs{position:absolute}
a{color:inherit;text-decoration:none}

/* top bar */
.topbar{left:0;top:0;width:1200px;height:28px;background:var(--pink);color:#fff;font:500 15px var(--head);white-space:nowrap}
.topbar .call{left:140px;top:5px;display:flex;gap:7px;align-items:center}
.topbar .mail{left:650px;top:5px;display:flex;gap:8px;align-items:center}
.topbar .socials{left:985px;top:8px;display:flex;gap:14px}
.topbar .socials span{width:12px;height:12px;border-radius:50%;background:#fff;opacity:.9}

/* header */
.header{left:0;top:28px;width:1200px;height:81px;background:#fff}
.nav{top:36px;display:flex;font:500 15px var(--head);letter-spacing:.3px;color:#222;white-space:nowrap}
.nav-left{left:127px;gap:33px}
.nav-right{left:739px;gap:30px}
.brand-mark{left:536px;top:-2px;width:64px;height:64px;border-radius:50%;background:#fff;border:3px solid var(--pink-soft)}
.brand-name{left:0;width:1147px;text-align:center;top:36px;font:500 26px var(--head);color:var(--pink);white-space:nowrap}

/* hero */
.hero{left:0;top:109px;width:1200px;height:603px;
  background:radial-gradient(ellipse at 45% 55%,#d9577f 0,#b94466 18%,rgba(120,80,60,.0) 40%),
  linear-gradient(180deg,#4a3a30 0%,#6b5546 45%,#8a7660 75%,#a39478 100%)}
.hero-title{left:520px;width:655px;top:98px;text-align:center;color:#fff;font:700 44px var(--head);letter-spacing:.5px;white-space:nowrap}
.hero-sub{left:520px;width:655px;top:156px;text-align:center;color:#fff;font:400 35px var(--head);white-space:nowrap}
.btn-action{left:757px;top:220px;width:180px;height:43px;background:var(--pink);color:#fff;font:600 18px var(--head);display:flex;align-items:center;justify-content:center}
.car-arrow{top:268px;width:40px;height:40px;border-radius:50%;background:#222;display:flex;align-items:center;justify-content:center}
.bump{width:130px;height:24px;background:#fff;border-radius:70px 70px 0 0;display:flex;justify-content:center;padding-top:2px}

/* features */
.feature{top:800px;width:220px;text-align:center}
.feature .ring{margin:0 auto;width:101px;height:101px;border-radius:50%;border:2.5px solid var(--pink-soft);display:flex;align-items:center;justify-content:center}
.feature .ring span{width:60px;height:60px;border-radius:50%;border:2px solid var(--blush)}
.feature h3{margin-top:33px;font:500 18px var(--head);color:#222}
.feature p{margin-top:14px;font:400 13px/26px var(--head);color:#555}
.feature .more{display:inline-block;margin-top:12px;width:98px;height:30px;border:2px solid var(--pink);border-radius:4px;color:var(--pink);font:400 13px/26px var(--head)}

/* welcome */
.welcome{left:0;top:1206px;width:1200px;height:553px;background:linear-gradient(135deg,#e45b9d,#e56aa4 50%,#e25499)}
.welcome .kicker{left:143px;top:75px;color:#fff;font:400 25px var(--head)}
.welcome h2{left:143px;top:106px;color:#fff;font:700 38px var(--head);white-space:nowrap}
.welcome .rule{left:143px;top:164px;width:72px;height:3px;background:#fff}
.welcome p{left:143px;top:188px;width:460px;color:#fff;font:400 14.5px/27.3px var(--body)}
.welcome .btn-ghost{left:143px;top:405px;width:137px;height:40px;border:2px solid #fff;border-radius:2px;color:#fff;font:600 15px/36px var(--head);text-align:center}
.welcome .frame{left:629px;top:77px;width:422px;height:364px;border:2px solid #fff;border-radius:6px}
.welcome .photo{left:639px;top:88px;width:418px;height:362px;border-radius:4px;background:linear-gradient(135deg,#dfe6ea,#b9c7d2 40%,#6f8aa8 60%,#e9e2d6)}

/* blog */
.blog-title{left:0;width:1200px;top:1838px;text-align:center;font:400 39px var(--head);color:var(--navy)}
.blog-title b{font-weight:700}
.blog-rule{left:568px;top:1913px;width:64px;height:3px;background:var(--navy)}
.card{width:283px;height:361px;background:#fff;box-shadow:0 0 6px rgba(0,0,0,.15);padding:7px}
.card .img{height:184px;position:relative}
.card .date{position:absolute;right:0;bottom:0;width:56px;height:52px;background:var(--pink);color:#fff;font:500 14px/18px var(--head);text-align:center;padding-top:8px}
.card h4{margin:22px 0 0 0;padding:0 7px;font:500 15.5px/24px var(--head);color:#222}
.card p{margin:14px 0 0 0;padding:0 9px;font:400 12px/24px var(--head);color:#666}

/* quote */
.quote{left:0;top:2453px;width:1200px;height:634px;background:linear-gradient(180deg,#f08592,#ef8894 60%,#ee8c97)}
.quote-photo{left:560px;top:2418px;width:620px;height:669px;border-radius:300px 300px 0 0;background:linear-gradient(180deg,#e9c58f 0%,#f1d7c4 30%,#f5f0ec 60%,#5a5a5a 80%,#e3cfc4 100%)}
.qbox{left:143px;top:2516px;width:458px;height:463px;border:3px solid #fff}
.qbox .mark{left:30px;top:36px;width:54px;height:54px;border-radius:50%;border:3px solid #fff}
.qbox .h1{left:101px;top:30px;color:#fff;font:700 27px var(--head)}
.qbox .h2{left:101px;top:62px;color:#fff;font:400 27px var(--head)}
.field{left:32px;width:321px;height:34px;background:#fff;border:1px solid #eee;font:400 11px var(--head);color:#555;padding:10px 14px}
.submit{left:32px;top:381px;width:223px;height:41px;background:var(--pink);color:#fff;font:600 15px/41px var(--head);text-align:center}

/* footer */
.footer{left:0;top:3087px;width:1200px;height:404px;background:var(--footer)}
.f-mark{left:243px;top:70px;width:50px;height:50px;border-radius:50%;border:3px solid var(--pink-soft)}
.f-name{left:138px;top:130px;width:320px;font:500 25px var(--head);color:var(--pink);white-space:nowrap}
.f-text{left:140px;top:178px;width:280px;font:400 13px/24px var(--head);color:#333}
.f-social{left:140px;top:300px;display:flex;gap:10px}
.f-social span{width:33px;height:33px;border-radius:50%;border:2px solid var(--pink)}
.f-h{font:600 18px var(--head);color:#111;white-space:nowrap}
.contact-row{left:468px;display:flex;gap:16px;font:400 14px/23px var(--head);color:#222;white-space:nowrap}
.contact-row svg{flex:none;margin-top:4px}
.nl-text{left:785px;top:143px;width:280px;font:400 12.5px/22px var(--head);color:#333}
.nl-input{left:784px;width:273px;height:38px;border:1px solid #ccc;border-radius:20px;background:#fff;font:400 11px var(--head);color:#555;padding:12px 14px}
.subscribe{left:785px;top:298px;width:134px;height:35px;border-radius:20px;background:var(--pink);color:#fff;font:600 14px/35px var(--head);text-align:center}
.copyright{left:0;width:1200px;top:3542px;text-align:center;font:400 13px var(--head);color:#222}
</style>
</head>
<body>

<div class="abs topbar">
  <div class="abs call">
    <svg width="12" height="12" viewBox="0 0 24 24"><path fill="#fff" d="M6.6 10.8a15 15 0 006.6 6.6l2.2-2.2a1 1 0 011-.25 11.4 11.4 0 003.6.57 1 1 0 011 1V20a1 1 0 01-1 1A17 17 0 013 4a1 1 0 011-1h3.5a1 1 0 011 1 11.4 11.4 0 00.57 3.6 1 1 0 01-.25 1z"/></svg>
    Call Us : 1800 555 0142
  </div>
  <div class="abs mail">
    <svg width="14" height="11" viewBox="0 0 24 18"><rect x="1" y="1" width="22" height="16" rx="2" fill="#fff"/><path d="M1 2l11 8 11-8" stroke="#e34197" stroke-width="2" fill="none"/></svg>
    info@blueotterlantern-sample.com
  </div>
  <div class="abs socials" aria-label="Social links"><span></span><span></span><span></span><span></span></div>
</div>

<header class="abs header">
  <nav class="abs nav nav-left"><a>MAKE</a><a>SAVE</a><a>SPEND</a><a>SHARE</a></nav>
  <div class="abs brand-name">Blue Otter Lantern</div>
  <nav class="abs nav nav-right"><a>MISSION</a><a>GET STARTED</a><a>CONTACT BOL</a></nav>
</header>
<div class="abs brand-mark"></div>

<section class="abs hero" role="img" aria-label="Pink piggy bank being broken with a hammer, coins and banknotes spilling on a wooden table">
  <h1 class="abs hero-title">BLUE OTTER LANTERN</h1>
  <div class="abs hero-sub">Free Financial Advice</div>
  <a class="abs btn-action">TAKE ACTION</a>
  <div class="abs car-arrow" style="left:59px"><svg width="12" height="18" viewBox="0 0 12 18"><path d="M9 2L3 9l6 7" stroke="#fff" stroke-width="1.8" fill="none"/></svg></div>
  <div class="abs car-arrow" style="left:1106px"><svg width="12" height="18" viewBox="0 0 12 18"><path d="M3 2l6 7-6 7" stroke="#fff" stroke-width="1.8" fill="none"/></svg></div>
  <div class="abs bump" style="left:535px;top:579px">
    <svg width="18" height="24" viewBox="0 0 18 24"><path d="M9 1v20M2 14l7 7 7-7" stroke="#e34197" stroke-width="1.8" fill="none"/></svg>
  </div>
</section>

<section>
  <div class="abs feature" style="left:127px"><div class="ring"><span></span></div><h3>MAKE</h3><p>Sed ut perspiciatis unde omnis iste natus error sit voluptatem accusantium doloremque lum, totam rem aperiam</p><a class="more">Read More</a></div>
  <div class="abs feature" style="left:368px"><div class="ring"><span></span></div><h3>SAVE</h3><p>Sed ut perspiciatis unde omnis iste natus error sit voluptatem accusantium doloremque lum, totam rem aperiam</p><a class="more">Read More</a></div>
  <div class="abs feature" style="left:610px"><div class="ring"><span></span></div><h3>SPEND</h3><p>Sed ut perspiciatis unde omnis iste natus error sit voluptatem accusantium doloremque lum, totam rem aperiam</p><a class="more">Read More</a></div>
  <div class="abs feature" style="left:852px"><div class="ring"><span></span></div><h3>SHARE</h3><p>Sed ut perspiciatis unde omnis iste natus error sit voluptatem accusantium doloremque lum, totam rem aperiam</p><a class="more">Read More</a></div>
</section>

<section class="abs welcome">
  <div class="abs kicker">Welcome to</div>
  <h2 class="abs">Blue Otter Lantern</h2>
  <div class="abs rule"></div>
  <p class="abs">My mission is simple- I want to challenge you to rethink the way you think about growing, spending and saving money. By redesigning your life around your finances I want you to run your life as if you are the CEO of your own business, and the business is maximising the value and profitability of your life. It is shocking that in today's world of information we are we still live in a society where most educated people leave school without even</p>
  <a class="abs btn-ghost">READ MORE</a>
  <div class="abs frame"></div>
  <div class="abs photo" role="img" aria-label="Smiling man in a blue shirt discussing paperwork with a woman in a bright office"></div>
  <div class="abs bump" style="left:538px;top:529px">
    <svg width="18" height="24" viewBox="0 0 18 24"><path d="M9 1v20M2 14l7 7 7-7" stroke="#e34197" stroke-width="1.8" fill="none"/></svg>
  </div>
</section>

<h2 class="abs blog-title"><b>LATEST</b> BLOG</h2>
<div class="abs blog-rule"></div>

<article class="abs card" style="left:144px;top:1956px">
  <div class="img" role="img" aria-label="Couple talking at home while looking at a phone" style="background:linear-gradient(135deg,#c9ced2,#8f9a98 50%,#e2e0dc)"><div class="date">Oct 01<br>2019</div></div>
  <h4>Quis autem vel eum iure repre derit qui in ea voluptate</h4>
  <p>Sed ut perspiciatis unde omnis iste natus error sit voluptatem accusantium dmque lauantium, totam rem aperiam</p>
</article>
<article class="abs card" style="left:458px;top:1979px">
  <div class="img" role="img" aria-label="Hand holding a small piggy bank against warm blurred lights" style="background:linear-gradient(135deg,#6e2a1c,#c2452c 40%,#f0b07a 70%,#5a1e14)"><div class="date">Oct 01<br>2019</div></div>
  <h4>Quis autem vel eum iure repre derit qui in ea voluptate</h4>
  <p>Sed ut perspiciatis unde omnis iste natus error sit voluptatem accusantium dmque lauantium, totam rem aperiam</p>
</article>
<article class="abs card" style="left:772px;top:1956px">
  <div class="img" role="img" aria-label="Woman at a bright desk holding a green piggy bank" style="background:linear-gradient(135deg,#eef0ee,#d6dcd8 45%,#9fb08e 75%,#e8ebe6)"><div class="date">Oct 01<br>2019</div></div>
  <h4>Quis autem vel eum iure repre derit qui in ea voluptate</h4>
  <p>Sed ut perspiciatis unde omnis iste natus error sit voluptatem accusantium dmque lauantium, totam rem aperiam</p>
</article>

<section class="abs quote"></section>
<div class="abs quote-photo" role="img" aria-label="Smiling woman with long hair holding an open laptop"></div>
<form class="abs qbox">
  <div class="abs mark"></div>
  <div class="abs h1">REQUEST</div>
  <div class="abs h2">A FREE QUOTE</div>
  <div class="abs field" style="top:112px">First Name</div>
  <div class="abs field" style="top:161px">Company Name</div>
  <div class="abs field" style="top:209px">Email Address</div>
  <div class="abs field" style="top:257px">Phone Number</div>
  <div class="abs field" style="top:305px;height:53px">Message :</div>
  <div class="abs submit">SUBMIT NOW</div>
</form>

<footer class="abs footer">
  <div class="abs bump" style="left:535px;top:-24px;background:var(--footer)">
    <svg width="18" height="24" viewBox="0 0 18 24"><path d="M9 1v20M2 14l7 7 7-7" stroke="#222" stroke-width="1.8" fill="none"/></svg>
  </div>
  <div class="abs f-mark"></div>
  <div class="abs f-name">Blue Otter Lantern</div>
  <p class="abs f-text">My mission is simple- I want to challenge you to rethink the way you think about growing, spending and saving money. By redesigning your life around</p>
  <div class="abs f-social" aria-label="Social links"><span></span><span></span><span></span></div>

  <h5 class="abs f-h" style="left:468px;top:98px">CONTACT US</h5>
  <div class="abs contact-row" style="top:144px">
    <svg width="16" height="20" viewBox="0 0 16 20"><path d="M8 0a7 7 0 00-7 7c0 5 7 13 7 13s7-8 7-13a7 7 0 00-7-7zm0 10a3 3 0 110-6 3 3 0 010 6z" fill="#e34197"/></svg>
    <div>Blue Otter Lantern<br>12 Harbour Lane, Halifax NS</div>
  </div>
  <div class="abs contact-row" style="top:196px">
    <svg width="16" height="16" viewBox="0 0 24 24"><path fill="#e34197" d="M6.6 10.8a15 15 0 006.6 6.6l2.2-2.2a1 1 0 011-.25 11.4 11.4 0 003.6.57 1 1 0 011 1V20a1 1 0 01-1 1A17 17 0 013 4a1 1 0 011-1h3.5a1 1 0 011 1 11.4 11.4 0 00.57 3.6 1 1 0 01-.25 1z"/></svg>
    <div>Phone: +1 (555) 010-4821<br>Fax: +1 (555) 010-4822</div>
  </div>
  <div class="abs contact-row" style="top:251px">
    <svg width="16" height="13" viewBox="0 0 24 18"><rect x="1" y="1" width="22" height="16" rx="2" fill="#e34197"/><path d="M1 2l11 8 11-8" stroke="#fff" stroke-width="2" fill="none"/></svg>
    <div>Email:<br>info@blueotterlantern-sample.com</div>
  </div>

  <h5 class="abs f-h" style="left:785px;top:96px">SIGN UP FOR NEWSLETTER</h5>
  <p class="abs nl-text">Excepteur sint occaecat cupidatat non proident, sunt in culpa qui officia deserunt</p>
  <div class="abs nl-input" style="top:193px">Enter name</div>
  <div class="abs nl-input" style="top:244px">Enter email</div>
  <div class="abs subscribe">SUBSCRIBE</div>
</footer>

<div class="abs copyright">Blue Otter Lantern © 2019 All Rights Reserved.</div>

</body>
</html>
```